SaaS Early tech startup business card design

Unique design for experience ecommerce platform company. the business cards will be used by executive members. conformance with color code is required.

```html
<!DOCTYPE html>
<html lang="en">
<head>
<meta charset="utf-8">
<title>Velora Business Card</title>
<link href="https://fonts.googleapis.com/css2?family=Roboto:wght@400;500;700;900&display=swap" rel="stylesheet">
<style>
  :root {
    --stage: #6b6868;
    --navy: #1f2034;
    --paper: #f3f3f4;
    --teal: #17a394;
    --teal-deep: #0f7f88;
    --ink: #2a2a2e;
    --tagline-light: #f1f1f1;
    --accent-faint: rgba(23, 163, 148, 0.18);
  }
  html, body {
    margin: 0;
    padding: 0;
    width: 1200px;
    height: 1200px;
    overflow: hidden;
    background: var(--stage);
    font-family: "Roboto", Arial, sans-serif;
  }
  .canvas {
    position: relative;
    width: 1200px;
    height: 1200px;
  }
  .card {
    position: absolute;
    width: 594px;
    height: 350px;
    border-radius: 20px;
    overflow: hidden;
  }
  .card--front { left: 299px; top: 198px; background: var(--navy); }
  .card--back { left: 292px; top: 637px; background: var(--paper); }

  .brand {
    position: absolute;
    text-align: center;
  }
  .brand__name {
    display: block;
    font-weight: 900;
    color: var(--teal);
    letter-spacing: -1px;
    line-height: 1;
  }
  .brand__tagline {
    display: block;
    font-weight: 400;
    white-space: nowrap;
  }
  .card--front .brand { left: 0; right: 0; top: 120px; }
  .card--front .brand__name { font-size: 86px; }
  .card--front .brand__tagline { font-size: 17px; letter-spacing: 6px; color: var(--tagline-light); margin-top: 8px; padding-left: 6px; }

  .card--back .brand { left: 60px; width: 240px; top: 124px; }
  .card--back .brand__name { font-size: 76px; }
  .card--back .brand__tagline { font-size: 13px; letter-spacing: 5px; color: var(--teal); margin-top: 6px; padding-left: 5px; }

  .corner-accent {
    position: absolute;
    border-radius: 50%;
    background: var(--accent-faint);
  }
  .card--front .corner-accent { width: 120px; height: 120px; right: -20px; bottom: -20px; }
  .card--back .corner-accent { width: 110px; height: 110px; left: -30px; bottom: -30px; }

  .contact {
    position: absolute;
    left: 355px;
    top: 76px;
    color: var(--ink);
  }
  .contact__name {
    margin: 0;
    font-size: 24px;
    font-weight: 700;
    color: var(--teal-deep);
    letter-spacing: -0.3px;
  }
  .contact__role {
    margin: 2px 0 0;
    font-size: 16px;
  }
  .contact__list {
    list-style: none;
    margin: 26px 0 0;
    padding: 0;
    font-size: 16px;
  }
  .contact__list li {
    display: flex;
    align-items: center;
    height: 22px;
  }
  .contact__list svg {
    width: 13px;
    height: 13px;
    margin-right: 17px;
    fill: var(--teal-deep);
  }
  .contact__address {
    margin: 8px 0 0;
    font-size: 16px;
    line-height: 22px;
    font-style: normal;
  }
</style>
</head>
<body>
<main class="canvas">
  <section class="card card--front">
    <div class="brand">
      <span class="brand__name">Velora</span>
      <span class="brand__tagline">BUILT AROUND YOU</span>
    </div>
    <div class="corner-accent"></div>
  </section>

  <section class="card card--back">
    <div class="brand">
      <span class="brand__name">Velora</span>
      <span class="brand__tagline">BUILT AROUND YOU</span>
    </div>
    <div class="corner-accent"></div>

    <div class="contact">
      <h1 class="contact__name">Rami K.</h1>
      <p class="contact__role">CTO/Owner</p>
      <ul class="contact__list">
        <li>
          <svg viewBox="0 0 16 16" aria-hidden="true"><path d="M2 6c0-2 2.5-3 6-3s6 1 6 3v1h-3V5.5H5V7H2z"/><path d="M4 8h8l1.5 5h-11z"/></svg>
          (00) 0123 VELO
        </li>
        <li>
          <svg viewBox="0 0 16 16" aria-hidden="true"><path d="M1 3h14v10H1z M2.5 4.5v0.4L8 9l5.5-4.1v-0.4z M2.5 6.6v5h11v-5L8 10.7z" fill-rule="evenodd"/></svg>
          hello@velora.io
        </li>
        <li>
          <svg viewBox="0 0 16 16" aria-hidden="true"><path d="M8 1a7 7 0 1 0 0 14A7 7 0 0 0 8 1zm0 1.5c.8 0 1.7 1.5 2 4H6c.3-2.5 1.2-4 2-4zM2.6 6.5h2c-.1 1-.1 2 0 3h-2a5.6 5.6 0 0 1 0-3zm3.4 0h4a13 13 0 0 1 0 3H6a13 13 0 0 1 0-3zm5.4 0h2a5.6 5.6 0 0 1 0 3h-2c.1-1 .1-2 0-3zM6 11h4c-.3 1.6-1.1 2.5-2 2.5S6.3 12.6 6 11z"/></svg>
          www.velora.io
        </li>
      </ul>
      <address class="contact__address">Cedar Tower, Dubai<br>Tech Park District, UAE</address>
    </div>
  </section>
</main>
</body>
</html>
```